Small Business Broker Business Card Design

A business card design for a small business brokerage, which is a financial service, not unlike real estate brokerage, but for small businesses such as laundromats, pizza shops, restaurants, cleaners etc. The designs should all be simple, more conservative in nature, using the colors and font of the logo. Again, think real estate Brokerage as a business context
Contact Information for Business Card
Name: Glen R. Harlow. Title: Small Business Advisor. Email: g.harlow@bayfieldcapitalworks.example. Mobile: (555) 274-3918. Office: (555) 806-2147. www.bayfieldcapitalworks.example

```html
<!DOCTYPE html>
<html lang="en">
<head>
<meta charset="utf-8">
<title>Bayfield Capital Works – Business Card</title>
<link rel="stylesheet" href="https://fonts.googleapis.com/css2?family=Roboto+Condensed:wght@400;700&display=swap">
<style>
  :root {
    --stage: #222224;
    --card-dark: #1f1f23;
    --brand-green: #8cc63f;
    --brand-green-deep: #6e9f2c;
    --brand-blue: #1a3a6e;
    --band-blue: #1e4a78;
    --text-light: #f2f2f2;
  }
  * { box-sizing: border-box; margin: 0; padding: 0; }
  html, body {
    width: 1200px; height: 780px; overflow: hidden;
    background: var(--stage);
    font-family: "Roboto Condensed", Arial, sans-serif;
  }
  .stage {
    position: relative; width: 1200px; height: 780px;
    display: flex; align-items: center; justify-content: center; gap: 40px;
  }
  .card {
    position: relative; width: 540px; height: 309px; overflow: hidden;
    box-shadow: 0 14px 30px rgba(0,0,0,.45);
  }

  /* Front */
  .card--front { background: var(--card-dark); }
  .brand-lockup {
    position: absolute; left: 46px; top: 34px; width: 320px;
  }
  .brand-lockup__name {
    color: var(--brand-blue); font-weight: 700; font-size: 19px;
    letter-spacing: 1.2px; text-transform: uppercase; line-height: 1;
  }
  .brand-lockup__tagline {
    margin-top: 5px; color: var(--brand-green); font-size: 9px;
    letter-spacing: 1.3px; text-transform: uppercase;
  }
  .contact-band {
    position: absolute; left: 0; bottom: 0; width: 340px; height: 130px;
    background: linear-gradient(90deg, var(--brand-green) 0%, #4f8a63 45%, var(--band-blue) 100%);
    clip-path: polygon(0 0, 100% 0, 82% 100%, 0 100%);
  }
  .contact-list {
    position: absolute; left: 22px; top: 18px; list-style: none;
    color: var(--text-light); font-size: 14px; line-height: 1.6;
  }
  .contact-list li { display: flex; align-items: center; gap: 9px; white-space: nowrap; }
  .contact-list svg { width: 13px; height: 13px; flex: none; }
  .person {
    position: absolute; right: 40px; top: 104px; text-align: left;
  }
  .person__name {
    color: var(--brand-green); font-weight: 700; font-size: 30px; line-height: 1;
  }
  .person__title {
    margin-top: 6px; color: var(--text-light); font-size: 15px; line-height: 1.2;
  }
  .edge-accent {
    position: absolute; right: 0; top: 132px; width: 12px; height: 40px;
    background: var(--brand-green);
  }

  /* Back */
  .card--back {
    background: var(--brand-green);
    display: flex; flex-direction: column; align-items: center; justify-content: center;
  }
  .back-lockup__name {
    color: var(--brand-green-deep); font-weight: 700; font-size: 26px;
    letter-spacing: 1.5px; text-transform: uppercase; line-height: 1.1;
  }
  .back-lockup__tagline {
    margin-top: 6px; color: var(--brand-green-deep); font-size: 11px;
    letter-spacing: 1.6px; text-transform: uppercase;
  }
</style>
</head>
<body>
<main class="stage">

  <section class="card card--front" aria-label="Business card front">
    <div class="brand-lockup">
      <p class="brand-lockup__name">Bayfield Capital Works, Inc</p>
      <p class="brand-lockup__tagline">Steady guidance for every main street sale</p>
    </div>

    <div class="person">
      <h1 class="person__name">Glen R. Harlow</h1>
      <p class="person__title">Small Business Advisor</p>
    </div>
    <div class="edge-accent"></div>

    <div class="contact-band">
      <ul class="contact-list">
        <li>
          <svg viewBox="0 0 16 16" aria-hidden="true"><rect x="4" y="1" width="8" height="14" rx="1.5" fill="none" stroke="#1a3a6e" stroke-width="1.6"/><circle cx="8" cy="12.5" r="0.9" fill="#1a3a6e"/></svg>
          (555) 274-3918
        </li>
        <li>
          <svg viewBox="0 0 16 16" aria-hidden="true"><path d="M3 2l3 0 1.2 3-1.8 1.3a8 8 0 0 0 4.3 4.3L11 8.8l3 1.2v3c0 .6-.5 1-1 1A12 12 0 0 1 2 3c0-.5.4-1 1-1z" fill="#1a3a6e"/></svg>
          (555) 806-2147
        </li>
        <li>
          <svg viewBox="0 0 16 16" aria-hidden="true"><circle cx="8" cy="8" r="6.5" fill="none" stroke="#1a3a6e" stroke-width="1.5"/><ellipse cx="8" cy="8" rx="2.8" ry="6.5" fill="none" stroke="#1a3a6e" stroke-width="1.2"/><line x1="1.5" y1="8" x2="14.5" y2="8" stroke="#1a3a6e" stroke-width="1.2"/></svg>
          www.bayfieldcapitalworks.example
        </li>
        <li>
          <svg viewBox="0 0 16 16" aria-hidden="true"><rect x="1.5" y="3.5" width="13" height="9" rx="1" fill="none" stroke="#1a3a6e" stroke-width="1.5"/><path d="M2 4.5l6 4.5 6-4.5" fill="none" stroke="#1a3a6e" stroke-width="1.4"/></svg>
          g.harlow@bayfieldcapitalworks.example
        </li>
      </ul>
    </div>
  </section>

  <section class="card card--back" aria-label="Business card back">
    <p class="back-lockup__name">Bayfield Capital Works, Inc</p>
    <p class="back-lockup__tagline">Steady guidance for every main street sale</p>
  </section>

</main>
</body>
</html>
```